Elevating our current Business Card Design

We want to elevate our current business card with a new design to look like a zenith 300 company. We are a premium lubricant distributor (oil and grease).
We need 2 versions, version 1 is as per the uploaded a copy of our current business card with the English version.
For our Chinese version we need to use the front to be English in English and have the back of the card designed exactly like the front for all info to be in Chinese.
The design template needs to be such that we can amend the template with adding different information for each person's card.
The background colour of the card can be changed- we just need to clearly see all information on the card and logos.
The QJR and Ember steady logos cannot have any colour or display changes- only use the logos attached.
All logos need to be included and all information from the attached current card

```html
<!DOCTYPE html>
<html lang="en">
<head>
<meta charset="utf-8">
<title>Northgate Business Card – Front and Back</title>
<link rel="stylesheet" href="https://fonts.googleapis.com/css2?family=Open+Sans:wght@400;600;700;800&display=swap">
<style>
  :root {
    --stage: #232323;
    --card-dark: #1d1c21;
    --card-light: #ffffff;
    --red: #e52a25;
    --red-deep: #8e1419;
    --gold: #e3a92c;
    --ink: #1c1c1c;
    --badge-orange: #ef7a1e;
    --badge-grey: #8d8d8d;
    --eco-green: #1f4a2b;
  }
  * { box-sizing: border-box; margin: 0; padding: 0; }
  html, body { width: 1200px; height: 780px; overflow: hidden; }
  body {
    background: var(--stage);
    font-family: "Open Sans", Arial, sans-serif;
    display: flex;
    align-items: center;
    justify-content: center;
    gap: 40px;
  }
  .card {
    position: relative;
    width: 540px;
    height: 330px;
    border-radius: 18px;
    overflow: hidden;
  }

  /* Back of card */
  .card--back {
    background: var(--card-dark);
    box-shadow: 0 0 0 1px #2e2d33;
    display: flex;
    align-items: center;
    justify-content: center;
  }
  .brand-name {
    font-size: 66px;
    font-weight: 800;
    color: var(--red);
    letter-spacing: 1px;
    line-height: 1;
  }

  /* Front of card */
  .card--front { background: var(--card-light); }
  .front-band { position: absolute; inset: 0; width: 100%; height: 100%; }
  .identity {
    position: absolute;
    right: 26px;
    top: 22px;
    text-align: right;
    color: #fff;
  }
  .identity__name { font-size: 27px; font-weight: 600; line-height: 1.1; }
  .identity__title { font-size: 13.5px; font-weight: 400; letter-spacing: .3px; }

  .contact {
    position: absolute;
    left: 26px;
    bottom: 22px;
    color: var(--ink);
    font-size: 13px;
    line-height: 1.4;
  }
  .contact__address { margin-bottom: 10px; }
  .contact__list { list-style: none; }
  .contact__item { display: flex; align-items: center; gap: 8px; }
  .contact__icon { width: 12px; height: 12px; flex: none; }

  .partners {
    position: absolute;
    right: 22px;
    bottom: 24px;
    width: 250px;
  }
  .partners__certs {
    display: flex;
    justify-content: flex-end;
    gap: 16px;
    margin-bottom: 8px;
    padding-right: 10px;
  }
  .cert-badge {
    width: 36px;
    height: 36px;
    border-radius: 50%;
    background: var(--badge-orange);
    box-shadow: 0 0 0 4px #fff, 0 0 0 6px var(--badge-grey);
  }
  .eco-member {
    display: flex;
    align-items: center;
    gap: 5px;
    margin-bottom: 6px;
  }
  .eco-member__dot { width: 14px; height: 14px; border-radius: 50%; background: var(--eco-green); }
  .eco-member__text { font-size: 10px; font-weight: 700; color: var(--eco-green); line-height: 1.05; }
  .eco-member__sub { display: block; font-size: 6px; letter-spacing: .6px; }

  .supply-strip { display: flex; height: 46px; }
  .supply-strip__distributor {
    flex: 1;
    border: 1.5px solid var(--red);
    display: flex;
    align-items: center;
    padding: 0 10px;
    background: #fff;
  }
  .supply-strip__full { font-size: 9px; font-weight: 700; color: var(--red); line-height: 1.2; }
  .supply-strip__supplier {
    width: 108px;
    background: var(--red);
    color: #fff;
    display: flex;
    flex-direction: column;
    justify-content: center;
    align-items: center;
  }
  .supply-strip__brand { font-size: 17px; font-weight: 800; letter-spacing: .5px; line-height: 1; }
  .supply-strip__tag { font-size: 6.5px; font-weight: 600; letter-spacing: .4px; }
</style>
</head>
<body>

  <section class="card card--back" aria-label="Card back">
    <p class="brand-name">NORTHGATE</p>
  </section>

  <section class="card card--front" aria-label="Card front">
    <svg class="front-band" viewBox="0 0 540 330" preserveAspectRatio="none" aria-hidden="true">
      <defs>
        <linearGradient id="bandRed" x1="0" y1="0" x2="1" y2="0">
          <stop offset="0" stop-color="#ef2e27"/>
          <stop offset=".55" stop-color="#df2724"/>
          <stop offset="1" stop-color="#8e1419"/>
        </linearGradient>
      </defs>
      <path d="M0 0 H540 V96 C500,140 400,150 260,136 C150,125 60,118 0,132 Z" fill="url(#bandRed)"/>
      <path d="M540 102 C500,148 400,160 260,145 C150,134 60,126 12,150 C60,134 150,140 260,150 C400,166 505,150 540,108 Z" fill="var(--gold)"/>
    </svg>

    <div class="identity">
      <p class="identity__name">Marina Costa</p>
      <p class="identity__title">Administration Executive</p>
    </div>

    <div class="contact">
      <p class="contact__address">48 Harbour Freight Road<br>Riverton, WA 6155</p>
      <ul class="contact__list">
        <li class="contact__item">
          <svg class="contact__icon" viewBox="0 0 12 12" aria-hidden="true"><path d="M2 1 L4.5 1 L5 4 L3.6 5 C4.3 6.6 5.4 7.7 7 8.4 L8 7 L11 7.5 L11 10 C6 11 1 6 2 1 Z" fill="var(--red)"/></svg>
          1300 402 617
        </li>
        <li class="contact__item">
          <svg class="contact__icon" viewBox="0 0 12 12" aria-hidden="true"><rect x="3" y="0.5" width="6" height="11" rx="1.2" fill="none" stroke="var(--red)" stroke-width="1.2"/></svg>
          +61 412 808 341
        </li>
        <li class="contact__item">
          <svg class="contact__icon" viewBox="0 0 12 12" aria-hidden="true"><rect x="1" y="4" width="10" height="7" rx="1" fill="var(--red)"/><rect x="3" y="1" width="6" height="4" fill="none" stroke="var(--red)" stroke-width="1"/></svg>
          +61 8 9260 4415
        </li>
        <li class="contact__item">
          <svg class="contact__icon" viewBox="0 0 12 12" aria-hidden="true"><circle cx="6" cy="6" r="5.2" fill="var(--red)"/><path d="M1 6 H11 M6 1 C3.5 4 3.5 8 6 11 M6 1 C8.5 4 8.5 8 6 11" fill="none" stroke="#fff" stroke-width=".8"/></svg>
          www.northgatelube.com
        </li>
        <li class="contact__item">
          <svg class="contact__icon" viewBox="0 0 12 12" aria-hidden="true"><rect x="0.5" y="2.5" width="11" height="8" rx="1" fill="var(--red)"/><path d="M1 3 L6 7 L11 3" fill="none" stroke="#fff" stroke-width="1"/></svg>
          marina.costa@northgatelube.com
        </li>
      </ul>
    </div>

    <div class="partners">
      <div class="partners__certs">
        <span class="cert-badge" role="img" aria-label="QJR certification badge"></span>
        <span class="cert-badge" role="img" aria-label="QJR certification badge"></span>
        <span class="cert-badge" role="img" aria-label="QJR certification badge"></span>
      </div>
      <div class="eco-member">
        <span class="eco-member__dot"></span>
        <p class="eco-member__text">Ember steady<span class="eco-member__sub">NETWORK MEMBER</span></p>
      </div>
      <div class="supply-strip">
        <div class="supply-strip__distributor">
          <span class="supply-strip__full">NORTHGATE<br>LUBRICANT DISTRIBUTORS</span>
        </div>
        <div class="supply-strip__supplier">
          <span class="supply-strip__brand">KORVAN</span>
          <span class="supply-strip__tag">PREMIUM LUBRICANTS</span>
        </div>
      </div>
    </div>
  </section>

</body>
</html>
```